Dental clinic brochure design (Z fold)

We need a new brochure design made for our dental clinic - Corvellan Dental Surgery. One side is in English, the other is in Vietnamese - all text and translations provided in brochure sample with further instructions in word doc. We require a brochure design in a Z fold to convey a family friendly dental clinic, incorporating our logo colour into the theme and designers choice on complimentary colours. Additional high quality images are provided for use if required or free to use own images.

Colors
33b8a4
00a990
86cfc6

Requirements
Must have
• Easy to read font, flows from text to pictures and page to page
• At least 2 dental images

```html
<!DOCTYPE html>
<html lang="en">
<head>
<meta charset="utf-8">
<title>Corvellan Dental Surgery – Z-fold brochure</title>
<link href="https://fonts.googleapis.com/css2?family=Noto+Sans:wght@400;600;700&display=swap" rel="stylesheet">
<style>
  :root {
    --teal: #00a990;
    --teal-mid: #33b8a4;
    --teal-soft: #86cfc6;
    --mint-bg: #e7f4ef;
    --mint-band: #b4ddd3;
    --ink: #1f2a2a;
    --muted: #555f5f;
    --white: #ffffff;
    --page: #e8eef8;
  }
  * { box-sizing: border-box; margin: 0; padding: 0; }
  html, body { width: 960px; height: 1200px; overflow: hidden; }
  body {
    background: var(--page);
    font-family: "Noto Sans", Arial, sans-serif;
    color: var(--ink);
    position: relative;
  }
  .brochure {
    position: absolute;
    left: 10px; top: 265px;
    width: 940px; height: 670px;
    box-shadow: 0 6px 18px rgba(40, 60, 90, .18);
    overflow: hidden;
    background: var(--white);
  }
  .panel { position: absolute; top: 0; height: 670px; }
  .panel--scheme { left: 0; width: 316px; background: var(--teal); }
  .panel--promo { left: 316px; width: 308px; background: var(--white); }
  .panel--providers { left: 624px; width: 316px; background: var(--mint-bg); }
  .providers-band {
    position: absolute; left: 0; bottom: 0; width: 100%; height: 40px;
    background: var(--mint-band);
  }

  .photo-kids {
    position: absolute; left: 40px; top: 42px; width: 245px; height: 141px;
    border-radius: 0 22px 0 22px;
    background: linear-gradient(120deg, #f4e3c9 0%, #f7d36a 35%, #e98a9c 60%, #cfe27a 100%);
  }
  .scheme-kicker {
    position: absolute; left: 38px; top: 200px;
    color: var(--white); font-size: 21px; font-weight: 600; line-height: 1.2;
  }
  .scheme-title {
    position: absolute; left: 38px; top: 226px;
    color: var(--white); font-size: 29px; font-weight: 700; line-height: 1.2;
  }
  .scheme-body {
    position: absolute; left: 40px; top: 268px; width: 250px;
    color: var(--white); font-size: 11.2px; line-height: 15.5px;
  }
  .scheme-check {
    position: absolute; left: 40px; top: 328px;
    color: var(--white); font-size: 11.2px;
  }
  .scheme-phone {
    position: absolute; left: 39px; top: 345px;
    color: var(--white); font-size: 22px; font-weight: 700;
  }
  .photo-patient {
    position: absolute; left: 39px; top: 383px; width: 553px; height: 246px;
    border-radius: 0 30px 0 30px;
    background: linear-gradient(100deg, #dcd7cf 0%, #b8aee6 28%, #e8c1a6 55%, #c98a6a 80%, #4a3524 100%);
    z-index: 2;
  }

  .promo-title {
    position: absolute; left: 31px; top: 120px;
    color: var(--teal); font-size: 28px; font-weight: 700; line-height: 28px;
  }
  .promo-list { position: absolute; left: 31px; top: 204px; width: 240px; list-style: none; }
  .promo-item {
    position: relative; padding-left: 22px;
    font-size: 11.2px; line-height: 15px; color: var(--ink);
    margin-bottom: 23px;
  }
  .promo-item svg { position: absolute; left: 0; top: 2px; width: 12px; height: 12px; }
  .promo-item .indent { padding-left: 6px; }

  .providers-title {
    position: absolute; left: 28px; top: 60px;
    color: var(--teal); font-size: 27px; font-weight: 700; white-space: nowrap;
  }
  .providers-card {
    position: absolute; left: 28px; top: 112px; width: 247px; height: 436px;
    background: var(--white); border-radius: 0 20px 0 20px;
  }
  .provider { position: absolute; left: 23px; display: flex; gap: 7px; }
  .provider-avatar {
    width: 33px; height: 33px; flex: none;
    background: linear-gradient(180deg, var(--teal-mid), var(--teal));
  }
  .provider-name { font-size: 11.2px; font-weight: 700; line-height: 14px; }
  .provider-creds { font-size: 8.6px; color: var(--muted); line-height: 12px; margin-top: 2px; width: 175px; }
  .map-area {
    position: absolute; left: 47px; top: 269px; width: 147px; height: 165px;
    background: linear-gradient(160deg, #f4f6f6, #e4ecea);
  }

  .address-box {
    position: absolute; left: 27px; top: 558px; width: 245px; height: 87px;
    background: var(--teal); color: var(--white);
    border-radius: 26px 0 26px 0; text-align: center; z-index: 2;
  }
  .address-title { font-size: 15px; font-weight: 700; margin-top: 8px; line-height: 20px; }
  .address-line { font-size: 10.4px; line-height: 15px; }
</style>
</head>
<body>
<main class="brochure">
  <section class="panel panel--scheme">
    <div class="photo-kids" role="img" aria-label="Group of smiling children brushing their teeth"></div>
    <p class="scheme-kicker">Child Dental Scheme</p>
    <h1 class="scheme-title">Benefits Schedule</h1>
    <p class="scheme-body">A dental benefits program is available for eligible children aged 2 to 17 and will receive $1000 for dental treatments every 2 years.</p>
    <p class="scheme-check">To check if your children are eligible call us on</p>
    <p class="scheme-phone">(03) 9000 4182</p>
  </section>

  <div class="photo-patient" role="img" aria-label="Patient with braces smiling during a dental check-up"></div>

  <section class="panel panel--promo">
    <h2 class="promo-title">Special<br>Promotions</h2>
    <ul class="promo-list">
      <li class="promo-item">
        <svg viewBox="0 0 12 12"><circle cx="6" cy="6" r="5.2" fill="none" stroke="#00a990" stroke-width="1.2"/><path d="M3.4 6.2l1.8 1.7 3.4-3.5" fill="none" stroke="#00a990" stroke-width="1.2"/></svg>
        Gap free dental check-up, clean &amp; x-rays<br>for all health insurances**
      </li>
      <li class="promo-item">
        <svg viewBox="0 0 12 12"><circle cx="6" cy="6" r="5.2" fill="none" stroke="#00a990" stroke-width="1.2"/><path d="M3.4 6.2l1.8 1.7 3.4-3.5" fill="none" stroke="#00a990" stroke-width="1.2"/></svg>
        At home whitening kit now $199 limited<br>time only (normally $395)
      </li>
      <li class="promo-item">
        <svg viewBox="0 0 12 12"><circle cx="6" cy="6" r="5.2" fill="none" stroke="#00a990" stroke-width="1.2"/><path d="M3.4 6.2l1.8 1.7 3.4-3.5" fill="none" stroke="#00a990" stroke-width="1.2"/></svg>
        *Conditions apply —<br><span class="indent">Ask staff for more information</span>
      </li>
    </ul>
  </section>

  <section class="panel panel--providers">
    <div class="providers-band"></div>
    <h2 class="providers-title">Dental Providers</h2>
    <div class="providers-card">
      <div class="provider" style="top:21px">
        <div class="provider-avatar" role="img" aria-label="Dentist avatar"></div>
        <div><p class="provider-name">Dr Mai Vorel</p><p class="provider-creds">BDSc (Hons), GDipOH</p></div>
      </div>
      <div class="provider" style="top:66px">
        <div class="provider-avatar" role="img" aria-label="Dentist avatar"></div>
        <div><p class="provider-name">Dr Quan Tessar</p><p class="provider-creds">BDSc (Hons), MDSc, FCDA, GradDipCD Implant Surgery</p></div>
      </div>
      <div class="provider" style="top:121px">
        <div class="provider-avatar" role="img" aria-label="Dentist avatar"></div>
        <div><p class="provider-name">Dr Linh Avery</p><p class="provider-creds">BOHSc, MDent (Gen)</p></div>
      </div>
      <div class="provider" style="top:171px">
        <div class="provider-avatar" role="img" aria-label="Dentist avatar"></div>
        <div><p class="provider-name">Dr Paul Renwick</p><p class="provider-creds">BOHSc, MDent (Gen), FCDA</p></div>
      </div>
      <div class="provider" style="top:221px">
        <div class="provider-avatar" role="img" aria-label="Dentist avatar"></div>
        <div><p class="provider-name">Dr Kira Solan</p><p class="provider-creds">BDS (Hons)</p></div>
      </div>
      <div class="map-area" role="img" aria-label="Street map showing the clinic location near the station"></div>
    </div>
    <div class="address-box">
      <p class="address-title">Address</p>
      <p class="address-line">48 Larkmoor Road Westvale, VIC 3021</p>
      <p class="address-line">Phone: (03) 9000 4182</p>
      <p class="address-line">Email: admin@corvellandental.com.au</p>
    </div>
  </section>
</main>
</body>
</html>
```